business card deign

Logo needs the following on it.
1. attached logo
2. Tagline - "If it keeps the ice frosty or the night rolling...we bring it!"
3. Name- Dalton Pikes, Founder and CPO
4. Address - 412 E. Carver Avenue, Ste 2207, Marlow Bay, FL. 33917
5. Phone - 555.318.4726

```html
<!DOCTYPE html>
<html lang="en">
<head>
<meta charset="utf-8">
<title>Kelbrook Business Card</title>
<link href="https://fonts.googleapis.com/css2?family=Arimo:wght@400;700&display=swap" rel="stylesheet">
<style>
  :root {
    --bg: #3b3b3b;
    --card: #2d2d2d;
    --ink: #ffffff;
    --ink-soft: #d8d8d8;
    --silver: #bdbdbd;
  }
  * { margin: 0; padding: 0; box-sizing: border-box; }
  html, body { width: 1200px; height: 803px; overflow: hidden; }
  body {
    background: var(--bg);
    font-family: "Arimo", Arial, sans-serif;
    color: var(--ink);
    display: flex;
    align-items: center;
    justify-content: center;
    gap: 60px;
  }
  .card {
    width: 525px;
    height: 300px;
    background: var(--card);
    border-radius: 22px;
    position: relative;
    box-shadow: 0 14px 30px rgba(0,0,0,.35);
  }
  /* Front */
  .front .brand {
    position: absolute; left: 40px; top: 58px;
    font-size: 22px; font-weight: 700; letter-spacing: 14px;
  }
  .front .person { position: absolute; left: 40px; top: 104px; }
  .person-name { font-size: 17px; font-weight: 700; text-transform: uppercase; letter-spacing: -0.3px; }
  .person-role { font-size: 12px; color: var(--ink-soft); margin-top: 2px; }
  .address { font-size: 12px; line-height: 15px; color: var(--ink-soft); margin-top: 14px; }
  .contacts { list-style: none; margin-top: 14px; font-size: 12px; line-height: 16px; color: var(--ink-soft); }
  .contacts li { display: flex; align-items: center; gap: 8px; }
  .contacts svg { width: 11px; height: 11px; fill: var(--ink); }
  /* Back */
  .back { display: flex; flex-direction: column; align-items: center; justify-content: center; }
  .back .mark { width: 46px; height: 46px; border-radius: 50%; background: var(--silver); margin-bottom: 20px; }
  .back .brand {
    font-size: 34px; font-weight: 700; letter-spacing: 20px; margin-right: -20px; color: var(--silver);
  }
  .tagline { font-size: 13px; font-weight: 700; margin-top: 26px; }
</style>
</head>
<body>
  <section class="card front">
    <div class="brand">KELBROOK</div>
    <div class="person">
      <div class="person-name">Dalton Pikes</div>
      <div class="person-role">Founder and CPO</div>
      <div class="address">412 E. Carver Avenue<br>Ste 2207<br>Marlow Bay, FL. 33917</div>
      <ul class="contacts">
        <li><svg viewBox="0 0 12 12"><path d="M2.5 0.5l2 2.2-1 1.3c.7 1.6 2 2.9 3.6 3.6l1.3-1 2.2 2-1.3 2C4.8 12.2-.2 7.2.5 2z"/></svg>555.318.4726</li>
        <li><svg viewBox="0 0 12 12"><path d="M0 2h12v8H0zM1 3v.3L6 6.6l5-3.3V3z"/></svg>info@kelbrook.com</li>
        <li><svg viewBox="0 0 12 12"><circle cx="6" cy="6" r="5.5"/></svg>www.kelbrook.com</li>
      </ul>
    </div>
  </section>

  <section class="card back">
    <div class="mark"></div>
    <div class="brand">KELBROOK</div>
    <div class="tagline">If it keeps the ice frosty or the night rolling...we bring it!</div>
  </section>
</body>
</html>
```